Pinecrest Harbor Foundation Web Design

The design we need is for a WordPress blog that will be our content platform. We are a registered 501(c)3 non-profit that focuses on financially supporting the treatment of cancer patients that have been told they have no hope and there is nothing the conventional medical system can do for them. Through this wesbite we want to both rasie awareness about the treatment options plus, raise funds for treating patients. The two primary target audiences of the site are...

1. Terminally ill patients and their families to let them know that there is an option other then hospice and that we are hear to support that option.

2. People looking to help donate to a worthwhile cause that resonates with them.

The website is https://pinecrestharborfoundation.org/

See attached logo designs!!!

Target Market(s)

Cancer patients and their families

Industry/Entity Type

Foundation

Font styles to use
Sans Serif

Colors
ffffff
fbed22

Requirements
Must have
• I like this look of this site. It is clean, simple, helpful, soft. I like the flow of the pages.
• http://www.meadowsforcalm.org/
• I like the design and flow but NOT the color or boldness
• https://tvbn-youth.org/
• I like this style for a donation page.
• https://www.tumorstudyhub.org/we-are-tsh/join-the-cause/donations/one-time-donation
• with the addition of a Would you like your employer to match? button.
Nice to have
• White black and gold - but soft
• Even possibly grayscale like the site I like.

```html
<!DOCTYPE html>
<html lang="en">
<head>
<meta charset="utf-8">
<title>Pinecrest Harbor Foundation</title>
<link rel="stylesheet" href="https://fonts.googleapis.com/css2?family=Open+Sans:wght@400;600;700&family=Oswald:wght@500&display=swap">
<style>
:root{
  --charcoal:#333333;
  --charcoal-deep:#222222;
  --gold:#b8962e;
  --gold-bright:#fbed22;
  --gold-soft:#e8d27c;
  --ink:#2b2b2b;
  --muted:#8a8a8a;
  --gray-bg:#f3f2ee;
  --footer:#1f1f1f;
  --white:#ffffff;
}
*{box-sizing:border-box;margin:0;padding:0}
html,body{width:1200px;height:3158px;overflow:hidden}
body{font-family:"Open Sans",Arial,sans-serif;color:var(--ink);background:var(--white);position:relative}
.section{position:absolute;left:0;width:1200px}

/* header */
.site-header{top:0;height:126px;background:var(--white)}
.brand{position:absolute;left:99px;top:30px;display:flex;align-items:center;gap:12px}
.brand-dot{width:40px;height:40px;border-radius:50%;background:var(--gold)}
.brand-name{font-weight:700;font-size:21px;line-height:25px;color:var(--charcoal);width:180px}
.contact-row{position:absolute;right:99px;top:22px;display:flex;align-items:center;gap:14px;font-size:15px;color:var(--charcoal)}
.contact-icon{width:30px;height:30px;border-radius:50%;display:inline-flex;align-items:center;justify-content:center;margin-right:8px;vertical-align:middle}
.contact-icon.gold{background:var(--gold)}
.contact-icon.dark{background:var(--charcoal)}
.social-row{display:flex;gap:5px}
.social-row span{width:22px;height:22px;display:block;background:var(--charcoal)}
.social-row span:nth-child(even){background:var(--gold)}
.main-nav{position:absolute;right:99px;top:80px;display:flex;gap:54px;font-size:15px;font-weight:600;color:var(--ink)}

/* hero */
.hero{top:126px;height:512px;background:linear-gradient(90deg,#3a3633 0%,#5c5752 35%,#a8a39d 62%,#d9d6d2 80%,#eceae7 100%)}
.hero-title{position:absolute;left:99px;top:152px;font-family:"Oswald",Arial,sans-serif;font-weight:500;font-size:50px;color:var(--white)}
.hero-text{position:absolute;left:99px;top:238px;width:490px;font-size:15px;line-height:23px;color:var(--white)}
.btn-outline{position:absolute;border:2px solid var(--white);color:var(--white);font-size:14px;display:flex;align-items:center;justify-content:center}
.hero .btn-outline{left:99px;top:320px;width:120px;height:50px;font-size:15px}
.hero-arrow{position:absolute;top:238px}

/* features */
.features{top:638px;height:440px}
.features svg.band{position:absolute;left:0;top:0}
.feature{position:absolute;top:60px;width:240px;text-align:center;color:var(--white)}
.feature h3{font-weight:600;font-size:24px;margin-top:16px}
.feature p{font-size:14px;font-weight:600;line-height:23px;margin-top:14px;color:#dedbd3}
.feature .icon{height:80px;display:flex;justify-content:center;align-items:flex-end}
.seal{position:absolute;left:562px;top:276px;width:76px;height:76px;border-radius:50%;background:var(--white)}

/* headings */
.section-title{position:absolute;left:0;width:1200px;text-align:center;font-weight:700;font-size:28px;color:var(--charcoal)}
.rule{position:absolute;left:540px;width:120px;height:2px;background:var(--gold)}

/* about */
.about{top:1040px;height:423px}
.about p{position:absolute;left:110px;width:980px;text-align:center;font-size:13.5px;line-height:27px;color:var(--muted)}
.btn-solid{position:absolute;background:var(--charcoal);color:var(--white);font-size:15px;font-weight:700;display:flex;align-items:center;justify-content:center}

/* awareness */
.awareness{top:1463px;height:537px;background:var(--gray-bg)}
.promo{position:absolute;top:181px;width:486px;height:267px;display:flex}
.promo-body{width:240px;padding:24px 20px;color:var(--white);text-align:center}
.promo-body h3{font-size:19px;font-weight:700;line-height:26px}
.promo-body p{font-size:14px;line-height:23px;margin-top:12px}
.promo-body .btn-outline{position:static;margin:18px auto 0;width:124px;height:38px;font-size:13px}
.promo.dark .promo-body{background:var(--charcoal)}
.promo.gold .promo-body{background:var(--gold-soft);color:var(--ink)}
.promo.gold .btn-outline{border-color:var(--ink);color:var(--ink)}
.promo-photo{flex:1}

/* news */
.news{top:2000px;height:600px}
.news-item{position:absolute;top:185px;width:240px}
.news-photo{width:236px;height:236px;border-radius:50%}
.date-badge{position:absolute;left:158px;top:182px;width:60px;height:60px;border-radius:50%;font-size:15px;font-weight:700;line-height:18px;text-align:center;padding-top:12px}
.date-badge.dark{background:var(--charcoal);color:var(--white)}
.date-badge.gold{background:var(--gold-bright);color:var(--ink)}
.news-item p{margin-top:24px;font-size:15px;line-height:23px;text-align:center;padding:0 16px}

/* newsletter */
.newsletter{top:2600px;height:86px;background:var(--charcoal)}
.newsletter label{position:absolute;left:99px;top:30px;color:var(--white);font-weight:700;font-size:21px}
.newsletter .field{position:absolute;left:248px;top:22px;width:664px;height:44px;border:2px solid var(--white);color:var(--white);font-size:14px;padding:12px 14px}
.newsletter .submit{position:absolute;left:932px;top:22px;width:168px;height:44px;background:var(--gold-bright);color:var(--ink);font-weight:700;font-size:16px;display:flex;align-items:center;justify-content:center}

/* footer */
.site-footer{top:2686px;height:472px;background:var(--footer);color:var(--white)}
.footer-brand{position:absolute;left:0;width:1200px;top:56px;text-align:center}
.footer-brand .brand-dot{width:52px;height:52px;margin:0 auto;background:var(--gold-soft)}
.footer-brand .brand-name{color:var(--white);width:auto;font-size:22px;line-height:29px;margin-top:24px}
.footer-social{position:absolute;top:226px;left:0;width:1200px;display:flex;justify-content:center;gap:10px}
.footer-social span{width:42px;height:42px;border:2px solid var(--white);border-radius:50%}
.footer-nav{position:absolute;top:318px;left:0;width:1200px;display:flex;justify-content:center;gap:26px;font-size:15px;font-weight:600}
.footer-nav .sep{color:var(--gold-soft)}
.footer-line{position:absolute;left:99px;width:1002px;top:385px;height:1px;background:#8a8a8a}
.copyright{position:absolute;top:420px;left:0;width:1200px;text-align:center;font-size:13px;font-weight:600}
</style>
</head>
<body>

<header class="section site-header">
  <div class="brand"><span class="brand-dot"></span><span class="brand-name">Pinecrest Harbor Foundation</span></div>
  <div class="contact-row">
    <span><span class="contact-icon gold"><svg width="16" height="12" viewBox="0 0 16 12"><rect x="0.5" y="0.5" width="15" height="11" fill="none" stroke="#fff"/><path d="M1 1l7 6 7-6" fill="none" stroke="#fff"/></svg></span>info@pinecrestharborfoundation.com</span>
    <span><span class="contact-icon dark"><svg width="14" height="14" viewBox="0 0 24 24"><path d="M6.6 10.8a15 15 0 006.6 6.6l2.2-2.2a1 1 0 011-.25 11 11 0 003.6.6 1 1 0 011 1V20a1 1 0 01-1 1A17 17 0 013 4a1 1 0 011-1h3.5a1 1 0 011 1 11 11 0 00.6 3.6 1 1 0 01-.25 1z" fill="#fff"/></svg></span>180 055 0142</span>
    <span class="social-row"><span></span><span></span><span></span><span></span><span></span></span>
  </div>
  <nav class="main-nav"><span>HOME</span><span>ABOUT US</span><span>CHARITY</span><span>SPONSORSHIP</span><span>TREATMENT</span><span>CONTACT US</span></nav>
</header>

<section class="section hero" role="img" aria-label="Smiling doctor in a white coat with a stethoscope speaking with a patient">
  <h1 class="hero-title">Pinecrest Harbor Foundation</h1>
  <p class="hero-text">Sed ut perspiciatis unde omnis iste natus error sit voluptatem accusantium doloremque laudantium.</p>
  <span class="btn-outline">Read More</span>
  <svg class="hero-arrow" style="left:34px" width="22" height="44" viewBox="0 0 22 44"><path d="M20 2L2 22l18 20" fill="none" stroke="#fff" stroke-width="2.5"/></svg>
  <svg class="hero-arrow" style="right:34px" width="22" height="44" viewBox="0 0 22 44"><path d="M2 2l18 20L2 42" fill="none" stroke="#fff" stroke-width="2.5"/></svg>
</section>

<section class="section features">
  <svg class="band" width="1200" height="440" viewBox="0 0 1200 440">
    <path d="M0 0H1200V414Q600 220 0 414Z" fill="#c9a43a"/>
    <path d="M0 0H1200V394Q600 250 0 394Z" fill="#333333"/>
  </svg>
  <div class="feature" style="left:80px">
    <div class="icon"><svg width="72" height="72" viewBox="0 0 72 72" fill="none" stroke="#e8d27c" stroke-width="4"><path d="M36 34L24 22a8 8 0 0112-10 8 8 0 0112 10z"/><path d="M6 48h12l14 6h16a5 5 0 010 10H28"/><path d="M48 58l14-8a5 5 0 016 8L50 68H6"/></svg></div>
    <h3>Charities</h3><p>Morbi diam mauris viverra in gravida eu matti</p>
  </div>
  <div class="feature" style="left:343px">
    <div class="icon"><svg width="76" height="76" viewBox="0 0 76 76" fill="#e8d27c"><circle cx="26" cy="12" r="8"/><circle cx="50" cy="12" r="8"/><path d="M10 34a16 16 0 0132 0v14H10z"/><path d="M34 34a16 16 0 0132 0v14H34z"/><path d="M38 74L24 60a8 8 0 0114-10 8 8 0 0114 10z" stroke="#333333" stroke-width="3"/></svg></div>
    <h3>Organisation</h3><p>Morbi diam mauris viverra in gravida eu matti</p>
  </div>
  <div class="feature" style="left:613px">
    <div class="icon"><svg width="76" height="72" viewBox="0 0 76 72" fill="none" stroke="#e8d27c" stroke-width="4"><rect x="24" y="4" width="40" height="24" fill="#e8d27c"/><circle cx="44" cy="16" r="6" fill="#333333" stroke="none"/><path d="M4 48h14l14 6h14a5 5 0 010 10H28"/><path d="M46 58l16-8a5 5 0 016 8L48 68H4"/></svg></div>
    <h3>Sponsorship</h3><p>Morbi diam mauris viverra in gravida eu matti</p>
  </div>
  <div class="feature" style="left:874px">
    <div class="icon"><svg width="72" height="72" viewBox="0 0 72 72" fill="#e8d27c"><path d="M36 22L26 12a7 7 0 0110-9 7 7 0 0110 9z"/><path d="M30 30C20 24 6 26 6 40c0 10 10 16 20 20l4 10h4V30z"/><path d="M42 30c10-6 24-4 24 10 0 10-10 16-20 20l-4 10h-4V30z"/></svg></div>
    <h3>Treatments</h3><p>Morbi diam mauris viverra in gravida eu matti</p>
  </div>
  <span class="seal"></span>
</section>

<section class="section about">
  <h2 class="section-title" style="top:20px">About Pinecrest Harbor Foundation</h2>
  <span class="rule" style="top:63px"></span>
  <p style="top:104px">Nemo enim ipsam voluptatem quia voluptas sit aspernatur aut odit aut fugit, sed quia consequuntur magni dolores eos qui ratione voluptatem sequi nesciunt. Neque porro quisquam est, qui dolorem ipsum quia dolor sit amet, consectetur, adipisci velit, sed quia non numquam eius modi tempora incidunt ut labore et dolore magnam aliquam quaerat voluptatem.</p>
  <p style="top:200px">Sed ut perspiciatis unde omnis iste natus error sit voluptatem accusantium doloremque laudantium, totam rem aperiam, eaque ipsa quae ab illo inventore veritatis et quasi architecto beatae vitae dicta sunt explicabo.</p>
  <span class="btn-solid" style="left:533px;top:290px;width:135px;height:50px">READ MORE</span>
</section>

<section class="section awareness">
  <h2 class="section-title" style="top:62px">Raise Awareness</h2>
  <span class="rule" style="top:114px"></span>
  <article class="promo dark" style="left:99px">
    <div class="promo-body">
      <h3>Treatment Options Plus</h3>
      <p>Lorem ipsum dolor sit amet, consectetur adipiscing elit. Aliquam pulvinar eleentum vestibulum. Quisque nec dignissim.</p>
      <span class="btn-outline">MORE DETAILS</span>
    </div>
    <div class="promo-photo" role="img" aria-label="Nurse caring for an elderly patient in a hospital bed" style="background:linear-gradient(135deg,#c9c2b8,#e8e4de 55%,#b4b4b4)"></div>
  </article>
  <article class="promo gold" style="left:615px">
    <div class="promo-body">
      <h3>Raise Funds For Treating Patients</h3>
      <p>Lorem ipsum dolor sit amet, consectetur adipiscing elit. Aliquam pulvinar eleentum vestibulum. Quisque nec dignissim.</p>
      <span class="btn-outline">MORE DETAILS</span>
    </div>
    <div class="promo-photo" role="img" aria-label="Older man smiling as a doctor rests a hand on his shoulder" style="background:linear-gradient(135deg,#a7a48e,#cfc6b8 45%,#5c5553 70%,#e9e6e3)"></div>
  </article>
</section>

<section class="section news">
  <h2 class="section-title" style="top:68px">Latest News</h2>
  <span class="rule" style="top:120px"></span>
  <article class="news-item" style="left:105px">
    <div class="news-photo" role="img" aria-label="Two hands clasped in comfort" style="background:radial-gradient(circle at 45% 45%,#c7a08a,#8f6a58 70%,#5e4a40)"></div>
    <span class="date-badge dark">MAR<br>10</span>
    <p>Duis aute irure dolor in reprehenderit in voluptate velit esse cillum.</p>
  </article>
  <article class="news-item" style="left:358px">
    <div class="news-photo" role="img" aria-label="Doctor wearing an awareness ribbon talking with a patient" style="background:radial-gradient(circle at 60% 40%,#f1ece7,#d9cbbd 60%,#8d7a6c)"></div>
    <span class="date-badge gold">APR<br>10</span>
    <p>Duis aute irure dolor in reprehenderit in voluptate velit esse cillum.</p>
  </article>
  <article class="news-item" style="left:606px">
    <div class="news-photo" role="img" aria-label="Medical staff attending a patient in a treatment room" style="background:radial-gradient(circle at 50% 50%,#d2d5d4,#a8b0b0 60%,#6d7676)"></div>
    <span class="date-badge dark">JAN<br>10</span>
    <p>Duis aute irure dolor in reprehenderit in voluptate velit esse cillum.</p>
  </article>
  <article class="news-item" style="left:855px">
    <div class="news-photo" role="img" aria-label="Doctor and smiling senior woman together" style="background:radial-gradient(circle at 50% 45%,#f0e8e0,#cdb29e 60%,#7d6656)"></div>
    <span class="date-badge gold">MAR<br>10</span>
    <p>Duis aute irure dolor in reprehenderit in voluptate velit esse cillum.</p>
  </article>
</section>

<section class="section newsletter">
  <label>NEWSLETTER:</label>
  <span class="field">Email Address</span>
  <span class="submit">SUBMIT</span>
</section>

<footer class="section site-footer">
  <div class="footer-brand"><span class="brand-dot" style="display:block"></span><div class="brand-name">Pinecrest Harbor<br>Foundation</div></div>
  <div class="footer-social"><span></span><span></span><span></span><span></span><span></span></div>
  <nav class="footer-nav"><span>HOME</span><span class="sep">|</span><span>ABOUT US</span><span class="sep">|</span><span>CHARITY</span><span class="sep">|</span><span>SPONSORSHIP</span><span class="sep">|</span><span>TREATMENT</span><span class="sep">|</span><span>CONTACT US</span></nav>
  <div class="footer-line"></div>
  <p class="copyright">Copyright © 2017 Pinecrest Harbor Foundation. All Right Reserved</p>
</footer>

</body>
</html>
```